Business Card, A4 Letter Head and DL Envelope for Brandvelle

We are looking for a design for our Business Card, A4 Letter Head and DL Envelope.

Brandvelle is a distributor of promotional products. We specialize in a range of branded promotional products, these include pens, polo shirts, key rings, drink bottles, uniforms and bags to name a few. We are experts in marketing and assist companies in choosing the right promotional product for their needs. We will predominately be an online business where customers visit our website and browse our range of promotional products and branding options.

Our colours are black, red, white and grey.

Files must be supplied in eps, pdf and ai format.

Please display the following information:
Derek Halloway
Account Manager
Suite xxx, 212 Ferrow Lane Melbourne, Victoria 3000
Phone +61 3 5550 1827
Mobile +61 455 016 342
sales@brandvelle-example.com.au
www.brandvelle-example.com.au

```html
<!DOCTYPE html>
<html lang="en">
<head>
<meta charset="utf-8">
<title>Brandvelle Stationery</title>
<link href="https://fonts.googleapis.com/css2?family=Arimo:wght@400;700&family=Michroma&display=swap" rel="stylesheet">
<style>
  :root {
    --red: #c01d24;
    --ink: #3a3a3a;
    --white: #ffffff;
    --ring: #d2d2d2;
    --faint: #ececec;
    --bg-light: #7a7a7a;
    --bg-dark: #555555;
  }
  * { margin: 0; padding: 0; box-sizing: border-box; }
  html, body { width: 1200px; height: 1000px; overflow: hidden; }
  body {
    background: radial-gradient(ellipse at 55% 45%, var(--bg-light), var(--bg-dark));
    font-family: "Arimo", Arial, sans-serif;
    position: relative;
  }
  .sheet { position: absolute; background: var(--white); box-shadow: 0 1px 4px rgba(0,0,0,.35); overflow: hidden; }
  .sheet > svg { position: absolute; left: 0; top: 0; }
  .abs { position: absolute; }

  .brand { display: flex; align-items: center; gap: 8px; }
  .brand-dot { border-radius: 50%; background: var(--red); flex: none; }
  .brand-name { font-family: "Arimo", Arial, sans-serif; font-weight: 700; color: var(--ink); letter-spacing: .5px; }

  /* Letterhead */
  .letterhead { left: 27px; top: 32px; width: 516px; height: 667px; }
  .letterhead .brand { left: 28px; top: 18px; }
  .letterhead .brand-dot { width: 28px; height: 28px; }
  .letterhead .brand-name { font-size: 16px; }
  .lh-contact { right: 26px; top: 14px; text-align: right; color: var(--white); font-size: 6.5px; line-height: 8.5px; }
  .lh-contact i { display: inline-block; width: 6px; height: 6px; border-radius: 50%; background: var(--white); margin-right: 3px; vertical-align: -0.5px; }
  .lh-footer { left: 0; bottom: 0; width: 100%; height: 21px; color: var(--white); font-size: 7px; text-align: center; line-height: 21px; }

  /* Business card front */
  .card-front { left: 601px; top: 100px; width: 413px; height: 246px; background: var(--red); }
  .card-name { right: 27px; top: 15px; font-family: "Michroma", sans-serif; font-size: 17px; color: #eeeeee; }
  .card-role { left: 213px; top: 39px; font-size: 12px; color: #f2f2f2; }
  .card-contact { left: 34px; top: 85px; color: var(--white); font-size: 12px; line-height: 15.5px; }
  .card-contact i { display: inline-block; width: 11px; height: 11px; border-radius: 50%; background: var(--white); margin-right: 5px; vertical-align: -1px; }
  .card-front .brand { left: 112px; top: 196px; }
  .card-front .brand-dot { width: 30px; height: 30px; }
  .card-front .brand-name { font-size: 15px; }

  /* Business card back */
  .card-back { left: 735px; top: 382px; width: 413px; height: 246px; background: var(--red); }
  .back-lockup { left: 140px; top: 38px; width: 270px; display: flex; flex-direction: column; align-items: center; }
  .back-lockup .brand-dot { width: 68px; height: 68px; margin-bottom: 34px; }
  .back-lockup .brand-name { font-size: 26px; }
  .back-url { margin-top: 8px; font-size: 11.5px; color: var(--red); }
  .back-url i { display: inline-block; width: 9px; height: 9px; border-radius: 50%; background: var(--red); margin-right: 5px; vertical-align: -1px; }

  /* DL envelope */
  .envelope { left: 311px; top: 713px; width: 612px; height: 268px; }
  .envelope .brand { left: 38px; top: 17px; }
  .envelope .brand-dot { width: 28px; height: 28px; }
  .envelope .brand-name { font-size: 16px; }
  .env-return { left: 40px; top: 72px; padding-left: 4px; border-left: 1px solid var(--red); font-size: 7px; line-height: 9px; color: var(--red); }
  .env-return .phone { color: var(--ink); }
  .env-return i { display: inline-block; width: 7px; height: 7px; border-radius: 50%; background: var(--red); margin-right: 3px; vertical-align: -1px; }
</style>
</head>
<body>

<section class="sheet letterhead" aria-label="A4 letterhead">
  <svg width="516" height="667" viewBox="0 0 516 667">
    <rect x="258" y="0" width="258" height="58" fill="var(--red)"/>
    <path d="M0 0 H250 A29 29 0 0 1 250 58 H0 Z" fill="var(--ring)"/>
    <path d="M0 0 H244 A29 29 0 0 1 244 58 H0 Z" fill="var(--white)"/>
    <circle cx="413" cy="540" r="50" fill="var(--faint)"/>
    <rect x="0" y="639" width="516" height="3" fill="var(--ring)"/>
    <rect x="0" y="646" width="516" height="21" fill="var(--red)"/>
  </svg>
  <div class="abs brand"><span class="brand-dot"></span><span class="brand-name">BRANDVELLE</span></div>
  <div class="abs lh-contact">
    <div><i></i>+61 455 016 342</div>
    <div><i></i>+61 3 5550 1827</div>
    <div><i></i>sales@brandvelle-example.com.au</div>
    <div><i></i>www.brandvelle-example.com.au</div>
  </div>
  <div class="abs lh-footer">Suite xxx, 212 Ferrow Lane Melbourne, Victoria 3000</div>
</section>

<section class="sheet card-front" aria-label="Business card front">
  <svg width="413" height="246" viewBox="0 0 413 246">
    <rect x="76" y="178" width="400" height="110" rx="34" fill="var(--ring)"/>
    <rect x="82" y="184" width="400" height="110" rx="28" fill="var(--white)"/>
  </svg>
  <div class="abs card-name">Derek Halloway</div>
  <div class="abs card-role">Account Manager</div>
  <div class="abs card-contact">
    <div><i></i>+61 455 016 342</div>
    <div><i></i>+61 3 5550 1827</div>
    <div><i></i>sales@brandvelle-example.com.au</div>
    <div>Suite xxx, 212 Ferrow Lane</div>
    <div>Melbourne, Victoria 3000</div>
  </div>
  <div class="abs brand"><span class="brand-dot"></span><span class="brand-name">BRANDVELLE</span></div>
</section>

<section class="sheet card-back" aria-label="Business card back">
  <svg width="413" height="246" viewBox="0 0 413 246">
    <circle cx="282" cy="123" r="160" fill="var(--ring)"/>
    <circle cx="285" cy="123" r="152" fill="var(--white)"/>
  </svg>
  <div class="abs back-lockup">
    <span class="brand-dot"></span>
    <span class="brand-name">BRANDVELLE</span>
    <div class="back-url"><i></i>www.brandvelle-example.com.au</div>
  </div>
</section>

<section class="sheet envelope" aria-label="DL envelope">
  <svg width="612" height="268" viewBox="0 0 612 268">
    <rect x="240" y="0" width="372" height="63" fill="var(--red)"/>
    <path d="M0 0 H226 A31.5 31.5 0 0 1 226 63 H0 Z" fill="var(--ring)"/>
    <path d="M0 0 H220 A31.5 31.5 0 0 1 220 63 H0 Z" fill="var(--white)"/>
    <circle cx="537" cy="192" r="40" fill="var(--faint)"/>
    <rect x="0" y="252" width="612" height="7" fill="var(--ring)"/>
  </svg>
  <div class="abs brand"><span class="brand-dot"></span><span class="brand-name">BRANDVELLE</span></div>
  <div class="abs env-return">
    <div class="phone"><i></i>+61 3 5550 1827</div>
    <div>Suite xxx, 212 Ferrow Lane</div>
    <div>Melbourne, Victoria 3000</div>
  </div>
</section>

</body>
</html>
```